Willow Creek Gatherings Event Planning in need of a design!!

Event Planning company, does a variety of events. I like simple more rustic designs focused on almond blossoms. We are based out of Northern California, the heart of almond country. I would like to see colors in light pinks, beige, light browns, whites or creams. the final design should communicate rustic simplicity. Below are some pictures of Almond blossoms and design ideas I prefer the one called Tulip Grove. Thanks

Target Market(s)

Women in the mid twenties and older. They should be in the upper middle class in need of an amazing party design and coordinator

Industry/Entity Type

Event Planning

Contact Information for Business Card

Maren Lockwood 530-624-0295almondbaffairs@gmail.comalmondblossomaffairs.com

Font styles to use
Other font styles liked:
• Amatic SC

Requirements
Must have
• almond blossom
• my information
• simplicity
Nice to have
• rustic design
• vintage feel
• whimsical
Should not have
• i like pink but not over the top

```html
<!DOCTYPE html>
<html lang="en">
<head>
<meta charset="utf-8">
<title>Maren Lockwood — Business Cards</title>
<link rel="stylesheet" href="https://fonts.googleapis.com/css2?family=Open+Sans:wght@400;600&display=swap">
<style>
  :root {
    --bg: #e9e4df;
    --card: #3a3334;
    --card-shade: #332d2e;
    --mint: #a8e2c3;
    --mint-dark: #8fcfae;
    --photo-light: #eef0ea;
    --photo-mid: #b9c9a6;
    --photo-blush: #e4b9b6;
  }
  * { box-sizing: border-box; margin: 0; padding: 0; }
  html, body { width: 1200px; height: 676px; overflow: hidden; }
  body {
    background: var(--bg);
    font-family: "Open Sans", Arial, sans-serif;
    position: relative;
  }
  .card {
    position: absolute;
    top: 190px;
    width: 520px;
    height: 297px;
    background: var(--card);
    border-radius: 4px;
    box-shadow: 0 8px 24px rgba(0,0,0,0.22);
    overflow: hidden;
  }
  .card--front { left: 60px; }
  .card--back { left: 620px; }

  .card__shade {
    position: absolute;
    inset: 0;
    background: linear-gradient(125deg, transparent 55%, var(--card-shade) 55%);
  }
  .blossom-photo {
    position: absolute;
    left: 40px;
    top: 30px;
    width: 230px;
    height: 160px;
  }
  .brand {
    position: absolute;
    display: flex;
    flex-direction: column;
    align-items: center;
    color: var(--mint);
  }
  .brand__mark {
    border-radius: 50%;
    background: var(--mint);
    border: 2px solid var(--card);
    box-shadow: 0 0 0 2px var(--mint);
  }
  .brand__name {
    font-weight: 600;
    white-space: nowrap;
    letter-spacing: 0.5px;
  }
  .card--front .brand { left: 290px; top: 62px; width: 200px; }
  .card--front .brand__mark { width: 70px; height: 70px; }
  .card--front .brand__name { font-size: 22px; margin-top: 8px; }

  .card--back .brand { left: 0; right: 0; top: 70px; }
  .card--back .brand__mark { width: 96px; height: 96px; }
  .card--back .brand__name { font-size: 32px; margin-top: 12px; }

  .contact {
    position: absolute;
    left: 250px;
    top: 196px;
    list-style: none;
    color: var(--mint);
    font-size: 14px;
    line-height: 24px;
  }
  .contact__item { display: flex; align-items: center; gap: 8px; }
  .contact__icon { width: 13px; height: 13px; flex: none; }
</style>
</head>
<body>
  <section class="card card--front">
    <div class="card__shade"></div>
    <svg class="blossom-photo" viewBox="0 0 230 160" role="img" aria-label="Photograph of white almond blossoms on a branch">
      <defs>
        <linearGradient id="blossomTones" x1="0" y1="0" x2="1" y2="1">
          <stop offset="0" stop-color="var(--photo-mid)"/>
          <stop offset="0.45" stop-color="var(--photo-light)"/>
          <stop offset="0.75" stop-color="var(--photo-blush)"/>
          <stop offset="1" stop-color="var(--photo-mid)"/>
        </linearGradient>
      </defs>
      <polygon points="0,0 230,0 230,100 180,135 0,135" fill="url(#blossomTones)"/>
      <polygon points="120,135 180,135 230,100 230,120 195,160 120,160" fill="var(--mint)"/>
    </svg>

    <div class="brand">
      <div class="brand__mark"></div>
      <div class="brand__name">Maren Lockwood</div>
    </div>

    <ul class="contact">
      <li class="contact__item">
        <svg class="contact__icon" viewBox="0 0 16 16"><path fill="var(--mint)" d="M3 2h3l1.5 3.5-2 1.2a8 8 0 0 0 3.8 3.8l1.2-2L14 10v3a1 1 0 0 1-1 1A11 11 0 0 1 2 3a1 1 0 0 1 1-1z"/></svg>
        530-817-4362
      </li>
      <li class="contact__item">
        <svg class="contact__icon" viewBox="0 0 16 16"><rect x="1" y="3" width="14" height="10" fill="var(--mint)"/><path d="M1 3l7 6 7-6" fill="none" stroke="var(--card)" stroke-width="1.3"/></svg>
        willowcgather@mailbox.test
      </li>
      <li class="contact__item">
        <svg class="contact__icon" viewBox="0 0 16 16"><circle cx="8" cy="8" r="7" fill="var(--mint)"/><path d="M1 8h14M8 1c-3 3-3 11 0 14M8 1c3 3 3 11 0 14" fill="none" stroke="var(--card)" stroke-width="1"/></svg>
        willowcreekgatherings.test
      </li>
    </ul>
  </section>

  <section class="card card--back">
    <div class="brand">
      <div class="brand__mark"></div>
      <div class="brand__name">Maren Lockwood</div>
    </div>
  </section>
</body>
</html>
```